Payment company requires web design

We need a web design for a new company based in Singapore.

The company focuses on providing 2 key products: 1) an alternative payment option (i.e. like quib or trelloquin options) on the traditional checkout process 2) a replacement/outsource of a merchants payment page. Key in the UX flow is a end customer dashboard that manages all payments.

We look to provide a simple, fluid and easy to use payment process. The dashboard is minimalistic that allows easy navigation, review of transactions and all available options through gamification.

The final design should communicate ease of use, flexibility and transparency.

Target Market(s)

The value is for the merchant - retail/travel/insurance companies. However its the merchant's end customers that are the target and who the UX is built for.

Industry/Entity Type

It Company

Logo Text

zelnar

Number of Pages Required

5+ page

Colors
ec1f27

Requirements
Must have
• 7 pages mimicking UX flow
• payment page * 2 - 1) alternative payment type 2) outsource of merchants payment page to our business
• our landing page
• end customer verification page
• end customer registration
• customer dashboard
• UX flow in attached file
Nice to have
• open to ideas
• have asked for the logo to be added
• logo to have the colour red (chinese for prosperity)
• the company is all about flexibility, transparency in personal finance management with the option of instalment payments

```html
<!DOCTYPE html>
<html lang="en">
<head>
<meta charset="utf-8">
<title>Zelnar — Payment Processing</title>
<link href="https://fonts.googleapis.com/css2?family=Open+Sans:wght@300;400;600;700&display=swap" rel="stylesheet">
<style>
:root{
  --brand-red:#e0242d;
  --brand-red-dark:#b5121b;
  --ink:#333333;
  --muted:#7a7a7a;
  --white:#ffffff;
  --footer-bg:#3b3b3b;
  --footer-bar:#2f2f2f;
  --footer-text:#c9c9c9;
  --rule:#e2e2e2;
  --illus-green:#2ecf7e;
}
*{box-sizing:border-box;margin:0;padding:0}
html,body{width:1200px;height:2769px;overflow:hidden}
body{font-family:"Open Sans",Arial,sans-serif;color:var(--ink);background:var(--white)}
.container{width:1052px;margin:0 auto;position:relative}

/* Hero */
.hero{position:relative;height:665px;overflow:hidden}
.hero-photo{position:absolute;inset:0;background:linear-gradient(120deg,#c7ccd4 0%,#9aa7b8 30%,#7b8ea8 55%,#5a6577 80%,#3f4450 100%)}
.hero-shade{position:absolute;inset:0;background:rgba(40,45,55,.25)}
.site-nav{position:absolute;top:40px;left:74px;right:74px;height:42px;display:flex;align-items:center}
.brand{font-size:31px;font-weight:700;color:var(--white);letter-spacing:.5px}
.nav-links{display:flex;list-style:none;margin-left:auto;gap:0}
.nav-links li{font-size:14px;font-weight:600;color:var(--white);margin-left:42px}
.nav-search{margin-left:40px;width:16px;height:16px}
.nav-actions{display:flex;gap:8px;margin-left:40px}
.btn{display:inline-flex;align-items:center;justify-content:center;font-size:14px;font-weight:600;border:2px solid transparent}
.btn-ghost{color:var(--white);border-color:var(--white);background:transparent}
.btn-solid{color:var(--white);background:var(--brand-red);border-color:var(--brand-red)}
.nav-actions .btn{height:40px;padding:0 16px}
.hero-copy{position:absolute;top:232px;left:0;right:0;text-align:center;color:var(--white)}
.hero-title{font-size:86px;font-weight:700;line-height:1;letter-spacing:1px}
.hero-tagline{font-size:33px;font-weight:600;margin-top:26px}
.hero-actions{display:flex;justify-content:center;gap:12px;margin-top:34px}
.hero-actions .btn{height:40px;padding:0 16px}
.slider-dots{position:absolute;top:618px;left:0;right:0;display:flex;justify-content:center;gap:6px}
.slider-dots span{width:10px;height:10px;border-radius:50%;background:var(--white)}
.slider-dots span.active{background:var(--brand-red)}

/* Sections */
.section-title{font-size:40px;font-weight:400;color:var(--brand-red);text-align:center;line-height:1}
.body-text{font-size:15.5px;line-height:28px;color:var(--muted)}
.btn-outline{height:50px;padding:0 34px;color:var(--ink);border:2px solid var(--brand-red);background:var(--white);font-size:15px}

.about{height:365px;padding-top:60px;text-align:center}
.about .body-text{margin-top:28px}
.about .btn-outline{margin-top:30px;width:152px}

.service{height:464px;background:linear-gradient(115deg,var(--brand-red-dark) 0%,#e3262f 40%,#e8353c 55%,#c8161e 75%,#b0111a 100%);color:var(--white);text-align:center;padding-top:58px;position:relative;overflow:hidden}
.service-curve{position:absolute;inset:0}
.service .section-title{color:var(--white)}
.service-lead{font-size:16px;margin-top:26px}
.service-grid{display:flex;justify-content:space-between;margin-top:50px}
.service-item{width:320px}
.service-icon{height:56px;display:flex;justify-content:center;align-items:center}
.service-name{font-size:19px;font-weight:600;margin-top:34px}
.service-text{font-size:15.5px;line-height:27px;margin-top:10px}

.faq{padding-top:62px;height:487px}
.faq-grid{display:grid;grid-template-columns:497px 497px;column-gap:58px;row-gap:34px;margin-top:40px}
.faq-q{font-size:19px;font-weight:700;color:var(--brand-red);line-height:24px}
.faq-a{font-size:15.5px;line-height:23px;color:var(--muted);margin-top:4px}
.faq .actions{text-align:center;margin-top:40px}
.faq .btn-outline{width:152px}
.divider{height:1px;background:var(--rule)}

.info{display:flex;justify-content:space-between;padding-top:50px;height:445px}
.info-copy{width:515px;padding-top:20px}
.info-title{font-size:40px;font-weight:400;color:var(--brand-red);line-height:1}
.info-copy .body-text{margin-top:30px}
.info-copy .btn-outline{margin-top:30px;width:152px}
.info-illustration{width:511px;height:321px;background:linear-gradient(135deg,#35d887,var(--illus-green) 60%,#23b86c)}

/* Footer */
.site-footer{background:var(--footer-bg);height:279px;padding-top:56px}
.footer-cols{display:flex}
.footer-col{width:268px}
.footer-col:nth-child(3){width:267px}
.footer-col h4{font-size:13.5px;font-weight:700;color:var(--white);text-transform:uppercase;letter-spacing:.3px}
.footer-col ul{list-style:none;margin-top:14px}
.footer-col li{font-size:13.5px;line-height:28.5px;color:var(--footer-text)}
.newsletter{width:244px}
.newsletter input{display:block;width:244px;height:44px;margin-top:14px;border:none;padding:0 12px;font-family:inherit;font-size:13px;color:#888}
.newsletter .btn{margin:14px 0 0 auto;height:40px;width:90px;font-size:14px;display:flex}
.footer-bar{background:var(--footer-bar);height:64px}
.footer-bar .container{display:flex;align-items:center;height:64px}
.copyright{font-size:13px;color:#9a9a9a}
.social{margin-left:auto;display:flex;gap:14px}
.social span{width:24px;height:24px;border-radius:3px;background:#8d8d8d}
</style>
</head>
<body>

<header class="hero">
  <div class="hero-photo" role="img" aria-label="Photo of a person holding a payment card next to a tablet and a cup of tea"></div>
  <div class="hero-shade"></div>
  <nav class="site-nav">
    <div class="brand">Zelnar</div>
    <ul class="nav-links">
      <li>Home</li><li>About Us</li><li>Services</li><li>Information</li><li>FAQ</li><li>Contact Us</li>
    </ul>
    <svg class="nav-search" viewBox="0 0 16 16" aria-label="Search"><circle cx="6.5" cy="6.5" r="4.5" fill="none" stroke="#fff" stroke-width="2"/><line x1="10" y1="10" x2="14.5" y2="14.5" stroke="#fff" stroke-width="2.2" stroke-linecap="round"/></svg>
    <div class="nav-actions">
      <span class="btn btn-ghost">Sign In</span>
      <span class="btn btn-solid">Register</span>
    </div>
  </nav>
  <div class="hero-copy">
    <h1 class="hero-title">Zelnar</h1>
    <p class="hero-tagline">We are payment processing company from Singapore</p>
    <div class="hero-actions">
      <span class="btn btn-ghost">Sign In</span>
      <span class="btn btn-solid">Register</span>
    </div>
  </div>
  <div class="slider-dots"><span class="active"></span><span></span><span></span><span></span></div>
</header>

<section class="about">
  <div class="container">
    <h2 class="section-title">About Us</h2>
    <p class="body-text">Aliquam molestie, mi et imperdiet euismod, dui purus auctor tellus, et interdum lacus lectus et ante. Sed accumsan sollicitudin sapien, sit amet adipiscing turpis gravida ac. In congue, neque ac lobortis volutpat, libero mauris varius mi, vitae suscipit ipsum ligula vitae risus. Duis aliquam nibh a dui iaculis viverra id a velit. Vivamus egestas risus in magna varius commodo. Sed semper viverra egestas.<br>Etiam pretium porttitor lectus, vel ornare neque porta volutpat.</p>
    <span class="btn btn-outline">Read More</span>
  </div>
</section>

<section class="service">
  <svg class="service-curve" viewBox="0 0 1200 464" preserveAspectRatio="none" aria-hidden="true">
    <path d="M380 0 C520 160 700 300 980 464" stroke="rgba(255,255,255,.12)" stroke-width="2" fill="none"/>
    <path d="M700 0 C760 180 900 330 1200 420" stroke="rgba(255,255,255,.10)" stroke-width="2" fill="none"/>
    <path d="M0 300 C300 240 560 300 820 464" stroke="rgba(255,255,255,.08)" stroke-width="2" fill="none"/>
  </svg>
  <div class="container">
    <h2 class="section-title">Customer Service</h2>
    <p class="service-lead">Aliquam molestie, mi et imperdiet euismod, dui purus auctor tellus, et interdum lacus lectus et ante.</p>
    <div class="service-grid">
      <div class="service-item">
        <div class="service-icon">
          <svg width="60" height="46" viewBox="0 0 60 46"><rect x="2" y="2" width="56" height="42" rx="4" fill="none" stroke="#fff" stroke-width="4"/><rect x="2" y="13" width="56" height="8" fill="#fff"/><rect x="10" y="30" width="18" height="5" fill="#fff"/></svg>
        </div>
        <h3 class="service-name">Merchant Payment</h3>
        <p class="service-text">Aliquam molestie, mi et imperdiet euismod, dui purus auctor tellus, etnterdum lacus lectus et ante.</p>
      </div>
      <div class="service-item">
        <div class="service-icon">
          <svg width="60" height="56" viewBox="0 0 60 56"><circle cx="18" cy="9" r="6" fill="#fff"/><circle cx="30" cy="7" r="6" fill="#fff"/><circle cx="42" cy="9" r="6" fill="#fff"/><path d="M10 30 v-10 a6 6 0 0 1 6 -6 h28 a6 6 0 0 1 6 6 v10z" fill="#fff"/><path d="M4 40 l14 -8 h10 l6 4 l6 -4 h10 l14 8 l-12 12 h-36z" fill="#fff"/><path d="M24 40 l6 4 l6 -4" stroke="#d11a22" stroke-width="2" fill="none"/></svg>
        </div>
        <h3 class="service-name">Outsourced Payment</h3>
        <p class="service-text">Aliquam molestie, mi et imperdiet euismod, dui purus auctor tellus, etnterdum lacus lectus et ante.</p>
      </div>
      <div class="service-item">
        <div class="service-icon">
          <svg width="62" height="42" viewBox="0 0 62 42"><rect x="2" y="2" width="58" height="38" rx="2" fill="none" stroke="#fff" stroke-width="4"/><rect x="8" y="8" width="46" height="26" fill="#fff"/><circle cx="31" cy="21" r="9" fill="#d11a22"/><rect x="29" y="15" width="4" height="12" fill="#fff"/></svg>
        </div>
        <h3 class="service-name">Instalment Payment</h3>
        <p class="service-text">Aliquam molestie, mi et imperdiet euismod, dui purus auctor tellus, etnterdum lacus lectus et ante.</p>
      </div>
    </div>
  </div>
</section>

<section class="faq">
  <div class="container">
    <h2 class="section-title">FAQ</h2>
    <div class="faq-grid">
      <div><h3 class="faq-q">Nam fermentum vestibulum purus id aliquet.?</h3><p class="faq-a">Aliquam molestie, mi et imperdiet euismod, dui purus auctor tellus, et interdum lacus lectus et ante. Sed accumsan sollicitudin sapien, sit amet adipiscing turpis gravida ac.</p></div>
      <div><h3 class="faq-q">Nam fermentum vestibulum purus id aliquet.?</h3><p class="faq-a">Aliquam molestie, mi et imperdiet euismod, dui purus auctor tellus, et interdum lacus lectus et ante. Sed accumsan sollicitudin sapien, sit amet adipiscing turpis gravida ac.</p></div>
      <div><h3 class="faq-q">Nam fermentum vestibulum purus id aliquet.?</h3><p class="faq-a">Aliquam molestie, mi et imperdiet euismod, dui purus auctor tellus, et interdum lacus lectus et ante. Sed accumsan sollicitudin sapien, sit amet adipiscing turpis gravida ac.</p></div>
      <div><h3 class="faq-q">Nam fermentum vestibulum purus id aliquet.?</h3><p class="faq-a">Aliquam molestie, mi et imperdiet euismod, dui purus auctor tellus, et interdum lacus lectus et ante. Sed accumsan sollicitudin sapien, sit amet adipiscing turpis gravida ac.</p></div>
    </div>
    <div class="actions"><span class="btn btn-outline">View All</span></div>
  </div>
</section>

<div class="container"><div class="divider"></div></div>

<section class="container info">
  <div class="info-copy">
    <h2 class="info-title">Information</h2>
    <p class="body-text">Aliquam molestie, mi et imperdiet euismod, dui purus auctor tellus, et interdum lacus lectus et ante. Sed accumsan sollicitudin sapien, sit amet adipiscing turpis gravida ac. In congue, neque ac lobortis volutpat, libero mauris varius mi, vitae suscipit ipsum ligula vitae risus. Duis aliquam nibh a dui iaculis viverra id a velit.</p>
    <span class="btn btn-outline">Read More</span>
  </div>
  <div class="info-illustration" role="img" aria-label="Illustration of a card payment at a terminal with a phone and a world map on green"></div>
</section>

<footer>
  <div class="site-footer">
    <div class="container footer-cols">
      <div class="footer-col"><h4>Site Map</h4><ul><li>Home</li><li>About Us</li><li>Services</li><li>Information</li><li>FAQ</li><li>Contact Us</li></ul></div>
      <div class="footer-col"><h4>Quick Links</h4><ul><li>Customer Offers</li><li>Legal</li><li>Blog</li><li>About us</li><li>Jobs</li><li>Press</li></ul></div>
      <div class="footer-col"><h4>Resources</h4><ul><li>Support</li><li>FAQ</li><li>Developers</li><li>Security</li></ul></div>
      <div class="footer-col newsletter"><h4>Newsletter Sign Up</h4><input type="text" placeholder="Enter Email Address"><span class="btn btn-solid">SIGN UP</span></div>
    </div>
  </div>
  <div class="footer-bar">
    <div class="container">
      <p class="copyright">Copyright © 2016. Company Name. All Right Reserved</p>
      <div class="social" aria-label="Social links"><span></span><span></span><span></span><span></span></div>
    </div>
  </div>
</footer>

</body>
</html>
```